Brightlane Rapid Rinse Web Design

We are looking for a web design that highlights our state of the art fully automated commercial vehicle washing equipment. Similar system to a car wash however this system is meant for the largest vehicles on our roadways. Transport trucks with or without a trailer, busses both highway and school, RV's from 5th wheel type to A Class. Cement trucks, dump trucks, vac trucks, fuel trucks etc. Pick ups with utility trailers...Refrigerator truck clean outs.
Brightlane Rapid Rinse will wash your vehicle quickly and with a minimal impact on the environment

Home page
About us
Why Brightlane
Services and pricing
Videos of wash system
Fleets
contact us

Target Market(s)

Commercial vehicle owners and operators as well as corporate fleets. Includes busses, municipal, school and highway.both school and

Industry/Entity Type

transportation

Coding

Coded - Design and coding required

Number of Pages Required

5+ page

Font styles to use
Sans Serif

Colors
0054AA
0677BA
7BADD7
CADEEF
E8F1F8

Requirements
Must have
• Welcome page,why us page which describes the financial and environmental benefits. payment processing page, contact us page, Services which is washing vehicles and greasing for commercial vehicles that want that service and grease
Nice to have
• pictures of both clean and dirty commercial vehicles ie. before and after

```html
<!DOCTYPE html>
<html lang="en">
<head>
<meta charset="utf-8">
<title>Brightlane Rapid Rinse</title>
<link href="https://fonts.googleapis.com/css2?family=Poppins:wght@400;500;600;700&family=Lato:wght@400;700&display=swap" rel="stylesheet">
<style>
:root{
  --blue:#0054AA;
  --blue-mid:#0677BA;
  --blue-soft:#7BADD7;
  --blue-pale:#CADEEF;
  --blue-mist:#E8F1F8;
  --ink:#111;
  --footer:#1b1b1d;
  --grey-band:#f3f3f3;
  --white:#fff;
}
*{margin:0;padding:0;box-sizing:border-box}
html,body{width:1200px;height:2676px;overflow:hidden}
body{font-family:'Lato',sans-serif;color:var(--ink);background:var(--white);position:relative}
.abs{position:absolute}
.topbar{left:0;top:0;width:1200px;height:51px;background:var(--blue);color:var(--white);font-family:'Poppins',sans-serif;font-size:13px;display:flex;justify-content:flex-end;align-items:center;padding-right:110px;gap:18px}
.topbar span{display:flex;align-items:center;gap:8px}
.nav{left:0;top:51px;width:1200px;height:85px;display:flex;align-items:center}
.brand{position:absolute;left:93px;top:20px;font-family:'Poppins',sans-serif;font-weight:700;font-size:22px;letter-spacing:.3px;color:var(--ink)}
.menu{position:absolute;left:476px;top:36px;display:flex;gap:44px;font-family:'Poppins',sans-serif;font-size:15px}
.menu a{color:var(--ink);text-decoration:none}
.menu a.active{color:var(--blue);text-decoration:underline;text-underline-offset:4px}
.nav-cta{position:absolute;left:987px;top:27px;width:120px;height:39px;border:1px solid var(--blue);color:var(--blue);font-family:'Poppins',sans-serif;font-size:14px;font-weight:500;display:flex;align-items:center;justify-content:center}
.hero{left:0;top:136px;width:1200px;height:577px;background:linear-gradient(90deg,#2c4a44 0%,#5b5750 12%,#9a9488 35%,#aaa59c 50%,#958f84 65%,#5a564f 88%,#2c4a44 100%)}
.hero-box{left:219px;top:104px;width:763px;height:391px;border:2px solid var(--white);text-align:center;color:var(--white);font-family:'Poppins',sans-serif;text-shadow:0 2px 6px rgba(0,0,0,.5)}
.hero-box .pre{margin-top:34px;font-size:27px;font-weight:600}
.hero-box h1{margin-top:6px;font-size:58px;font-weight:700;letter-spacing:1px;line-height:1.1}
.hero-box .sub{margin-top:10px;font-size:26px;letter-spacing:8px}
.hero-box .tag{margin-top:24px;font-size:26px;font-weight:600}
.hero-btns{display:flex;justify-content:center;gap:26px;margin-top:32px}
.btn{height:60px;display:flex;align-items:center;justify-content:center;font-family:'Poppins',sans-serif;font-size:20px;font-weight:600;text-shadow:none}
.btn-solid{width:189px;background:var(--white);color:var(--blue)}
.btn-ghost{width:188px;border:3px solid var(--white);color:var(--white);background:rgba(255,255,255,.18)}
.arrow{width:32px;height:32px}
.mission{left:0;top:713px;width:1200px;height:539px;background:var(--blue)}
.mission-photo{left:112px;top:781px;width:407px;height:535px;border:3px solid var(--white);background:linear-gradient(180deg,#b8b8b8,#c93b46 30%,#3a1f24 55%,#c93b46 75%,#9a9a9a)}
.mission-text{left:599px;top:772px;width:490px;color:var(--white)}
.mission-text h2{font-family:'Poppins',sans-serif;font-size:33px;font-weight:600}
.mission-text .lead{margin-top:16px;font-weight:700;font-size:16px;line-height:28px}
.mission-text p{font-size:15px;line-height:27.5px}
.mission-text .p1{margin-top:12px}
.mission-text .p2{margin-top:27px;text-align:justify}
.btn-read{margin-top:19px;width:144px;height:52px;background:var(--white);color:var(--blue);font-size:18px}
.services-title{left:0;top:1366px;width:1200px;text-align:center;font-family:'Poppins',sans-serif;font-size:36px;font-weight:600;color:var(--blue)}
.card{top:1445px;width:309px;height:340px}
.card .photo{width:100%;height:100%}
.card .label{position:absolute;left:0;bottom:0;width:296px;height:60px;background:var(--blue);clip-path:polygon(0 0,235px 0,100% 100%,0 100%);color:var(--white);font-size:19px;display:flex;align-items:center;padding-left:21px}
.ba{left:0;top:1852px;width:1200px;height:410px;background:var(--grey-band)}
.ba-photo{top:64px;width:476px;height:273px}
.ba-tag{position:absolute;left:14px;top:14px;background:var(--white);color:var(--blue);font-family:'Poppins',sans-serif;font-weight:600;font-size:17px;padding:6px 14px}
.footer{left:0;top:2262px;width:1200px;height:414px;background:var(--footer);color:var(--white)}
.footer-brand{left:110px;top:68px;font-family:'Poppins',sans-serif;font-weight:700;font-size:22px}
.socials{left:117px;top:145px;display:flex;gap:26px}
.socials span{width:32px;height:32px;border-radius:50%;background:var(--white)}
.fcol h4{font-family:'Poppins',sans-serif;font-weight:400;font-size:20px;margin-bottom:16px}
.fcol li{list-style:none;font-size:15px;height:34.5px;display:flex;align-items:center;gap:10px}
.contact-row{display:flex;gap:12px;font-size:15px;line-height:27px;margin-bottom:18px}
.contact-row .ico{width:32px;height:32px;border-radius:50%;background:var(--white);flex:none;display:flex;align-items:center;justify-content:center}
.footer-rule{left:112px;top:2578px;width:978px;height:1px;background:#e6e6e6}
.copy{left:0;top:2612px;width:1200px;text-align:center;font-size:16px;font-weight:700;color:var(--white)}
.bottom-strip{left:0;top:2668px;width:1200px;height:8px;background:var(--blue)}
</style>
</head>
<body>

<div class="abs topbar">
  <span><svg width="12" height="12" viewBox="0 0 24 24"><path fill="#fff" d="M6.6 10.8a15 15 0 0 0 6.6 6.6l2.2-2.2c.3-.3.7-.4 1-.2 1.1.4 2.3.6 3.6.6.6 0 1 .4 1 1V20c0 .6-.4 1-1 1A17 17 0 0 1 3 4c0-.6.4-1 1-1h3.5c.6 0 1 .4 1 1 0 1.3.2 2.5.6 3.6.1.3 0 .7-.2 1z"/></svg>Phone : +1 555 014 2290</span>
  <span>|</span>
  <span><svg width="14" height="11" viewBox="0 0 24 18"><path fill="#fff" d="M0 0h24v18H0z"/><path d="M1 1l11 8 11-8" stroke="#0054AA" stroke-width="2" fill="none"/></svg>Email : info@brightlanerinse.com</span>
</div>

<header class="abs nav">
  <div class="brand">BRIGHTLANE RAPID RINSE</div>
  <nav class="menu">
    <a class="active" href="#">HOME</a>
    <a href="#">ABOUT US</a>
    <a href="#">WHY BRIGHTLANE</a>
    <a href="#">MORE</a>
  </nav>
  <div class="nav-cta">CONTACT US</div>
</header>

<section class="abs hero" role="img" aria-label="White transport truck inside an automated wash bay between spinning brushes">
  <div class="abs hero-box">
    <div class="pre">WELCOME TO</div>
    <h1>BRIGHTLANE RAPID</h1>
    <div class="sub">RINSE</div>
    <div class="tag">SPEED (LESS THAN 15 MINUTES)</div>
    <div class="hero-btns">
      <div class="btn btn-solid">BOOK A WASH</div>
      <div class="btn btn-ghost">LEARN MORE</div>
    </div>
  </div>
  <svg class="abs arrow" style="left:33px;top:272px" viewBox="0 0 32 32"><circle cx="16" cy="16" r="15" fill="rgba(0,0,0,.35)"/><path d="M19 9l-7 7 7 7" stroke="#444" stroke-width="2.5" fill="none"/></svg>
  <svg class="abs arrow" style="left:1130px;top:272px" viewBox="0 0 32 32"><circle cx="16" cy="16" r="15" fill="#111"/><path d="M13 9l7 7-7 7" stroke="#fff" stroke-width="2.5" fill="none"/></svg>
</section>

<section class="abs mission"></section>
<div class="abs mission-photo" role="img" aria-label="Red and black wash brushes in an indoor truck wash bay"></div>
<div class="abs mission-text">
  <h2>OUR MISSION</h2>
  <div class="lead">Our dedication to revolutionizing truck washing with advanced technology and sustainable practices,</div>
  <p class="p1">At vero eos et accusamus et iusto odio dignissimos ducimus quiblan tiis pti nimi, id est laborum et dolorum fuga.</p>
  <p class="p2">Temporibus autem quibusdam et aut officiis debitisert autitr rerum necessaibus saepe eveniet ut et voluptates repuderaer iandae moles non recundae. Itaque earum rerum hic tenetuapiente deleus, ut aut reiciendis voluptatibus maiores alias consequatur aut perferendis doloribus asperiores repellat.</p>
  <div class="btn btn-read">READ MORE</div>
</div>

<h2 class="abs services-title">OUR SERVICES</h2>
<div class="abs card" style="left:111px">
  <div class="photo" role="img" aria-label="Trailer passing through red and black brushes" style="background:linear-gradient(90deg,#9ea4a8,#d8d8d6 45%,#b53a44 75%,#2a1c1f)"></div>
  <div class="label">Automated Truck Wash</div>
</div>
<div class="abs card" style="left:446px">
  <div class="photo" role="img" aria-label="Curtain-side trailer being washed in a wash bay" style="background:linear-gradient(90deg,#b0b4b6,#6b2a30 35%,#d9d9d6 55%,#d4c24a 80%,#c8c8c6)"></div>
  <div class="label">Additional Services</div>
</div>
<div class="abs card" style="left:778px">
  <div class="photo" role="img" aria-label="Row of white fleet trucks parked under an evening sky" style="background:linear-gradient(180deg,#7fa3c4,#d9c3b3 35%,#e6e8ea 55%,#7a7f86 80%,#5e646b)"></div>
  <div class="label">Fleet Services</div>
</div>

<section class="abs ba">
  <div class="abs ba-photo" style="left:111px;background:linear-gradient(180deg,#5f9ad6,#a9c9e8 45%,#8a8478 70%,#5b4c3c)" role="img" aria-label="Mud-covered dump truck on a dirt road before washing"><span class="ba-tag">BEFORE</span></div>
  <div class="abs ba-photo" style="left:614px;background:linear-gradient(90deg,#a8acae,#b8343e 20%,#e8e8e6 40%,#dcdcda 60%,#b8343e 80%,#a8acae)" role="img" aria-label="Clean white truck cab between wash brushes after washing"><span class="ba-tag">AFTER</span></div>
  <svg class="abs arrow" style="left:33px;top:187px" viewBox="0 0 32 32"><circle cx="16" cy="16" r="15" fill="#777"/><path d="M19 9l-7 7 7 7" stroke="#fff" stroke-width="2.5" fill="none"/></svg>
  <svg class="abs arrow" style="left:1130px;top:187px" viewBox="0 0 32 32"><circle cx="16" cy="16" r="15" fill="#111"/><path d="M13 9l7 7-7 7" stroke="#fff" stroke-width="2.5" fill="none"/></svg>
</section>

<footer class="abs footer">
  <div class="abs footer-brand">BRIGHTLANE RAPID RINSE</div>
  <div class="abs socials"><span></span><span></span><span></span><span></span></div>

  <div class="abs fcol" style="left:436px;top:68px">
    <h4>QUICK LINKS</h4>
    <ul>
      <li><svg width="12" height="12" viewBox="0 0 12 12"><path d="M0 6h9M6 2l4 4-4 4" stroke="#fff" stroke-width="2" fill="none"/></svg>Home</li>
      <li><svg width="12" height="12" viewBox="0 0 12 12"><path d="M0 6h9M6 2l4 4-4 4" stroke="#fff" stroke-width="2" fill="none"/></svg>About us</li>
      <li><svg width="12" height="12" viewBox="0 0 12 12"><path d="M0 6h9M6 2l4 4-4 4" stroke="#fff" stroke-width="2" fill="none"/></svg>Why Brightlane</li>
      <li><svg width="12" height="12" viewBox="0 0 12 12"><path d="M0 6h9M6 2l4 4-4 4" stroke="#fff" stroke-width="2" fill="none"/></svg>Services and pricing</li>
      <li><svg width="12" height="12" viewBox="0 0 12 12"><path d="M0 6h9M6 2l4 4-4 4" stroke="#fff" stroke-width="2" fill="none"/></svg>Videos of wash system</li>
    </ul>
  </div>
  <div class="abs fcol" style="left:655px;top:68px">
    <h4>HELP LINKS</h4>
    <ul>
      <li><svg width="12" height="12" viewBox="0 0 12 12"><path d="M0 6h9M6 2l4 4-4 4" stroke="#fff" stroke-width="2" fill="none"/></svg>FAQ</li>
      <li><svg width="12" height="12" viewBox="0 0 12 12"><path d="M0 6h9M6 2l4 4-4 4" stroke="#fff" stroke-width="2" fill="none"/></svg>Terms of use</li>
      <li><svg width="12" height="12" viewBox="0 0 12 12"><path d="M0 6h9M6 2l4 4-4 4" stroke="#fff" stroke-width="2" fill="none"/></svg>Privacy Policy</li>
      <li><svg width="12" height="12" viewBox="0 0 12 12"><path d="M0 6h9M6 2l4 4-4 4" stroke="#fff" stroke-width="2" fill="none"/></svg>Support Links</li>
      <li><svg width="12" height="12" viewBox="0 0 12 12"><path d="M0 6h9M6 2l4 4-4 4" stroke="#fff" stroke-width="2" fill="none"/></svg>Conditions</li>
    </ul>
  </div>
  <div class="abs fcol" style="left:831px;top:68px">
    <h4>CONTACT US</h4>
    <div class="contact-row"><span class="ico"><svg width="14" height="18" viewBox="0 0 14 18"><path d="M7 0a7 7 0 0 0-7 7c0 5 7 11 7 11s7-6 7-11a7 7 0 0 0-7-7z" fill="#1b1b1d"/><circle cx="7" cy="7" r="2.5" fill="#fff"/></svg></span><span>Brightlane Rapid Rinse<br>United States</span></div>
    <div class="contact-row" style="align-items:center"><span class="ico"><svg width="16" height="16" viewBox="0 0 24 24"><path fill="#1b1b1d" d="M6.6 10.8a15 15 0 0 0 6.6 6.6l2.2-2.2c.3-.3.7-.4 1-.2 1.1.4 2.3.6 3.6.6.6 0 1 .4 1 1V20c0 .6-.4 1-1 1A17 17 0 0 1 3 4c0-.6.4-1 1-1h3.5c.6 0 1 .4 1 1 0 1.3.2 2.5.6 3.6.1.3 0 .7-.2 1z"/></svg></span><span>+1 555 014 2290</span></div>
    <div class="contact-row" style="align-items:center"><span class="ico"><svg width="16" height="12" viewBox="0 0 24 18"><path d="M0 0h24v18H0z" fill="#1b1b1d"/><path d="M1 1l11 8 11-8" stroke="#fff" stroke-width="2" fill="none"/></svg></span><span>info@brightlanerinse.com</span></div>
  </div>
</footer>
<div class="abs footer-rule"></div>
<div class="abs copy">Copyrights@2024.Brightlane Rapid Rinse.All Rights Reserved</div>
<div class="abs bottom-strip"></div>

</body>
</html>
```